Business Card Design

New business card design

Target Market(s)

Residential & Commercial Property Managers

Industry/Entity Type

Plumbing Services

Contact Information for Business Card

Name - Rowan Keddle, title - Director, Phone Number - 0431 286 517, email - rowan@tbk-plumbing.com.au, Company ABN - 73 215 904 386,

Font styles to use
Sans Serif

Colors
0054AA
0677BA
7BADD7
CADEEF
E8F1F8

```html
<!DOCTYPE html>
<html lang="en">
<head>
<meta charset="utf-8">
<title>TBK Plumbing – Business Card</title>
<link href="https://fonts.googleapis.com/css2?family=Montserrat:wght@400;500;700&display=swap" rel="stylesheet">
<style>
  :root {
    --backdrop: #e3e1e2;
    --card-white: #ffffff;
    --card-blue: #2ca8e0;
    --ink: #1f2933;
    --drop-blue: #2ca8e0;
    --drop-white: #ffffff;
  }
  * { margin: 0; padding: 0; box-sizing: border-box; }
  html, body {
    width: 1200px; height: 1108px; overflow: hidden;
    background: var(--backdrop);
    font-family: "Montserrat", sans-serif;
    color: var(--ink);
  }
  .canvas { position: relative; width: 1200px; height: 1108px; }
  .card {
    position: absolute; left: 236px; width: 740px; height: 446px;
  }
  .card--front { top: 61px; background: var(--card-white); }
  .card--back { top: 580px; background: var(--card-blue); }

  .brand {
    position: absolute; display: flex; align-items: center;
    font-weight: 500; color: var(--ink); white-space: nowrap;
  }
  .brand__dot { border-radius: 50%; flex: none; }
  .card--front .brand { left: 70px; top: 205px; font-size: 38px; gap: 12px; }
  .card--front .brand__dot { width: 16px; height: 16px; background: var(--drop-blue); }
  .card--back .brand { left: 0; right: 0; justify-content: center; top: 180px; font-size: 74px; gap: 20px; }
  .card--back .brand__dot { width: 30px; height: 30px; background: var(--drop-white); }

  .divider {
    position: absolute; left: 373px; top: 148px; width: 2px; height: 186px;
    background: var(--ink);
  }
  .contact { position: absolute; left: 388px; top: 146px; }
  .contact__name { font-size: 26px; font-weight: 700; line-height: 1.2; }
  .contact__title { font-size: 16px; font-weight: 400; margin-top: 1px; }
  .contact__list { list-style: none; margin-top: 16px; }
  .contact__item {
    display: flex; align-items: center; gap: 10px;
    font-size: 16px; height: 31px;
  }
  .contact__icon { width: 17px; height: 17px; flex: none; fill: var(--ink); }
  .contact__abn { font-size: 16px; margin-top: 1px; }
  .contact__abn strong { font-weight: 700; }
</style>
</head>
<body>
<main class="canvas">
  <section class="card card--front" aria-label="Card front">
    <div class="brand"><span>tbk plumbing</span><span class="brand__dot"></span></div>
    <div class="divider"></div>
    <div class="contact">
      <h1 class="contact__name">Rowan Keddle</h1>
      <p class="contact__title">Director</p>
      <ul class="contact__list">
        <li class="contact__item">
          <svg class="contact__icon" viewBox="0 0 24 24" aria-hidden="true"><path d="M6.6 10.8a15.1 15.1 0 0 0 6.6 6.6l2.2-2.2a1 1 0 0 1 1-.25 11.4 11.4 0 0 0 3.6.57 1 1 0 0 1 1 1V20a1 1 0 0 1-1 1A17 17 0 0 1 3 4a1 1 0 0 1 1-1h3.5a1 1 0 0 1 1 1c0 1.25.2 2.45.57 3.57a1 1 0 0 1-.25 1z"/></svg>
          <span>0431 286 517</span>
        </li>
        <li class="contact__item">
          <svg class="contact__icon" viewBox="0 0 24 24" aria-hidden="true"><path d="M3 6h18v12H3z M3 6l9 7 9-7" fill="var(--ink)" stroke="#fff" stroke-width="1.5"/></svg>
          <span>rowan@tbk-plumbing.com.au</span>
        </li>
        <li class="contact__item">
          <svg class="contact__icon" viewBox="0 0 24 24" aria-hidden="true"><circle cx="12" cy="12" r="10"/><path d="M2 12h20M12 2c3 3 3 17 0 20M12 2c-3 3-3 17 0 20" stroke="#fff" stroke-width="1.4" fill="none"/></svg>
          <span>www.tbk-plumbing.com.au</span>
        </li>
      </ul>
      <p class="contact__abn"><strong>ABN</strong> - 73 215 904 386,</p>
    </div>
  </section>

  <section class="card card--back" aria-label="Card back">
    <div class="brand"><span>tbk plumbing</span><span class="brand__dot"></span></div>
  </section>
</main>
</body>
</html>
```